Certificates with Watermark Images

We are looking for a design of One page Certificates with Watermark (background) images where text will be printed over it .
Graphics design is required to reflect the flowing categories:
IPTV (Internet Protocol TV)
VoD (Video on Demand)
Satellite Receiver
Graphics design images for all three categories must be provided to maintain the same them .
Thank you and good luck.
Industry/Entity Type
Internet
Requirements
Must have
- Graphics design images for all three categories must be provided to maintain the same them

```html
<!DOCTYPE html>
<html lang="en">
<head>
<meta charset="utf-8">
<title>IPTV Company Certificate</title>
<link rel="stylesheet" href="https://fonts.googleapis.com/css2?family=Playfair+Display:wght@700&family=Libre+Baskerville:wght@400;700&display=swap">
<style>
  :root {
    --paper: #d5cfbf;
    --paper-light: #e0dbcd;
    --paper-dark: #a89e89;
    --stripe: rgba(150, 138, 115, 0.35);
    --frame: #f4f1ea;
    --title: #9e2a27;
    --ink: #1d1a16;
    --art-tone: #8c8270;
  }
  * { margin: 0; padding: 0; box-sizing: border-box; }
  html, body { width: 1200px; height: 848px; overflow: hidden; }
  body { background: var(--paper); }
  .certificate {
    position: relative;
    width: 1200px;
    height: 848px;
    overflow: hidden;
    background:
      radial-gradient(ellipse 70% 60% at 55% 45%, var(--paper-light) 0%, rgba(224,219,205,0) 70%),
      linear-gradient(180deg, rgba(0,0,0,0) 60%, rgba(140,128,105,0.35) 100%),
      var(--paper);
    font-family: "Libre Baskerville", "Times New Roman", serif;
    color: var(--ink);
  }
  .stripes {
    position: absolute;
    inset: 0 0 auto 0;
    height: 320px;
    background: repeating-linear-gradient(90deg, var(--stripe) 0 12px, rgba(0,0,0,0) 12px 26px);
    -webkit-mask-image: linear-gradient(180deg, #000 0%, rgba(0,0,0,0.5) 45%, transparent 100%);
    mask-image: linear-gradient(180deg, #000 0%, rgba(0,0,0,0.5) 45%, transparent 100%);
  }
  .art {
    position: absolute;
  }
  .art-ribbon {
    left: 310px; top: 28px; width: 580px; height: 170px;
    border-radius: 50% 50% 20% 20% / 60% 60% 20% 20%;
    background: radial-gradient(ellipse at 50% 40%, rgba(230,225,212,0.7), rgba(200,192,175,0.25) 70%, transparent);
  }
  .art-film {
    left: 370px; top: 520px; width: 770px; height: 300px;
    border-radius: 40% 30% 10% 10%;
    background: radial-gradient(ellipse 80% 70% at 70% 55%, rgba(120,110,92,0.45), rgba(150,140,120,0.15) 65%, transparent);
  }
  .art-screen {
    left: 50px; top: 578px; width: 320px; height: 190px;
    border-radius: 6px;
    background: linear-gradient(160deg, rgba(120,112,98,0.85), rgba(150,142,128,0.6));
  }
  .frame {
    position: absolute;
    inset: 22px 18px 22px 18px;
    border: 2px solid var(--frame);
    pointer-events: none;
  }
  .title {
    position: absolute;
    top: 52px; left: 0; width: 100%;
    text-align: center;
    font-family: "Playfair Display", "Bodoni Moda", serif;
    font-weight: 700;
    font-size: 58px;
    color: var(--title);
    letter-spacing: 0.5px;
  }
  .field-label {
    position: absolute;
    font-size: 18px;
    font-weight: 700;
  }
  .field-line {
    position: absolute;
    height: 2px;
    background: repeating-linear-gradient(90deg, var(--ink) 0 11px, transparent 11px 17px);
  }
</style>
</head>
<body>
<main class="certificate">
  <div class="stripes"></div>
  <div class="art art-ribbon" role="img" aria-label="Faint ribbon banner illustration behind the title"></div>
  <div class="art art-film" role="img" aria-label="Faint film strip and reel illustration"></div>
  <div class="art art-screen" role="img" aria-label="Television screen with film reels illustration"></div>
  <div class="frame"></div>

  <h1 class="title">IPTV Company</h1>

  <span class="field-label" style="left:148px; top:186px;">Name</span>
  <span class="field-line" style="left:220px; top:206px; width:872px;"></span>

  <span class="field-label" style="left:148px; top:284px;">Date</span>
  <span class="field-line" style="left:210px; top:302px; width:220px;"></span>

  <span class="field-label" style="left:487px; top:284px;">Type of Service</span>
  <span class="field-line" style="left:650px; top:302px; width:442px;"></span>

  <span class="field-label" style="left:148px; top:374px;">Reason for Award</span>
  <span class="field-line" style="left:340px; top:394px; width:752px;"></span>
  <span class="field-line" style="left:152px; top:457px; width:942px;"></span>
  <span class="field-line" style="left:152px; top:520px; width:942px;"></span>
</main>
</body>
</html>
```